Heating and Cooling Company mobile website

We need a website specifically designed for a viewing on a mobile device.

We serve the northern New Jersey heating, cooling and electrical residential market.

The goal is the drive traffic to the site by using Brintel Pay Per click. People will be searching for an HVAC contractor, and they land on our page. They need to get key info quickly without all the clutter of a desktop type of site.

Target Market(s)

Homeowners

Industry/Entity Type

Hvac

Coding

Coded - Design and coding required

Number of Pages Required

5+ page

Font styles to use
Serif

Requirements
Must have
• View attachments to see samples of the desktop version. It must have a similar color scheme
• The copy of the website is also attached
Nice to have
• Would like it to have a sort of Vardok feel to it. Make it seem like its an app that people are using and that its exciting to be on the website. It would be nice to have a page where customers can book appointments

```html
<!DOCTYPE html>
<html lang="en">
<head>
<meta charset="utf-8">
<title>Hearthline Climate – Heating &amp; Cooling</title>
<link rel="stylesheet" href="https://fonts.googleapis.com/css2?family=Fira+Sans:wght@400;500;600;700&family=Fira+Sans+Condensed:wght@500;600&display=swap">
<style>
:root{
  --parchment-light:#f3d89b;
  --parchment:#e6bd72;
  --parchment-deep:#d9a85a;
  --maroon:#8c1d2c;
  --maroon-dark:#5c1420;
  --maroon-footer:#9c2336;
  --orange:#ec8a2c;
  --navy:#1e2a4a;
  --steel:#8a9bb0;
  --white:#ffffff;
}
*{box-sizing:border-box;margin:0;padding:0}
html,body{width:1200px;height:2699px;overflow:hidden}
body{font-family:"Fira Sans",Arial,sans-serif;background:var(--parchment);position:relative}
.page{position:absolute;inset:0;width:1200px;height:2699px}
.abs{position:absolute}

.hero{left:0;top:0;width:1200px;height:1464px;
  background:radial-gradient(ellipse at 50% 40%,var(--parchment-light) 0%,var(--parchment) 60%,var(--parchment-deep) 100%)}

.brand{display:flex;align-items:center;gap:18px;color:var(--maroon);font-weight:700;font-size:58px;letter-spacing:1px;white-space:nowrap}
.brand-dot{width:34px;height:34px;border-radius:50%;background:var(--maroon);flex:none}
.brand-top{left:0;width:1200px;top:110px;justify-content:center}

.menu{left:946px;top:166px;display:flex;align-items:center;gap:28px;color:var(--maroon);font-weight:600;font-size:46px}
.menu-bars{width:50px;height:40px;display:flex;flex-direction:column;justify-content:space-between}
.menu-bars span{display:block;height:8px;background:var(--maroon);border-radius:2px}

.van{left:246px;top:377px;width:884px;height:420px;border-radius:60px 120px 40px 40px;z-index:1;
  background:linear-gradient(180deg,#9c2232 0%,#8c1d2c 45%,#1a1a1d 70%,#2b2b30 100%)}

.schedule{left:64px;top:248px;width:290px;height:230px;z-index:2}
.schedule-label{left:0;top:96px;width:290px;height:128px;display:flex;align-items:center;justify-content:center;text-align:center;color:var(--white);font-weight:700;font-size:36px;line-height:1.15}

.headline{left:0;width:1200px;top:830px;text-align:center;color:var(--maroon);font-weight:600;font-size:52px}

.learn-more{left:487px;top:942px;width:238px;height:100px;border-radius:50px;background:var(--maroon);border:6px solid var(--orange);
  color:var(--white);font-weight:600;font-size:32px;display:flex;align-items:center;justify-content:center}

.service-band{left:0;top:1049px;width:1200px;height:230px}

.services{left:0;top:1100px;width:1200px;height:330px}
.service{position:absolute;width:240px;text-align:center}
.service svg{display:block;margin:0 auto}
.service-name{margin-top:40px;color:var(--maroon);font-family:"Fira Sans Condensed","Arial Narrow",sans-serif;font-weight:600;font-size:32px;line-height:1.1}

.news{left:0;top:1464px;width:1200px;height:638px;
  background:linear-gradient(180deg,#3c4f60 0%,#4d5f6c 40%,#6b6458 70%,#8a7560 100%)}
.news-shade{left:0;top:1464px;width:1200px;height:638px;background:rgba(20,28,40,.35)}
.news-item{top:1615px;width:430px;color:var(--white)}
.news-date{text-align:center;font-weight:700;font-size:46px;margin-bottom:34px}
.news-text{font-size:27px;line-height:35px;text-align:justify}

.divider{left:0;top:2102px;width:1200px;height:20px;background:var(--steel)}

.footer-left{left:0;top:2122px;width:472px;height:577px;background:var(--maroon-dark)}
.footer-right{left:472px;top:2122px;width:728px;height:577px;background:var(--maroon-footer)}

.brand-plate{left:320px;top:1985px;width:560px;height:150px;border-radius:26px;background:var(--parchment-light);border:8px solid var(--orange);justify-content:center;font-size:46px;z-index:1}

.contact{left:0;top:2232px;width:472px;text-align:center;color:var(--white);font-size:30px;line-height:46.5px;font-style:normal}
.stay{left:0;top:2482px;width:472px;text-align:center;color:var(--white);font-weight:700;font-size:31px}
.social{left:116px;top:2551px;width:261px;height:101px;background:var(--orange);border:5px solid var(--parchment-light);border-radius:8px;display:flex;align-items:center;justify-content:center;gap:24px}
.social span{width:50px;height:50px;border-radius:50%;background:var(--white)}

.nav-list{list-style:none;color:var(--white)}
.nav-main{left:548px;top:2164px;font-size:28px;line-height:35px}
.nav-sub{left:861px;top:2170px;font-size:24px;line-height:35px}
.gap{height:35px}
.gap-sm{height:32px}
</style>
</head>
<body>
<div class="page">

  <section class="abs hero" aria-label="Introduction">
    <div class="abs brand brand-top"><span class="brand-dot"></span>Hearthline Climate</div>

    <div class="abs menu">Menu
      <div class="menu-bars"><span></span><span></span><span></span></div>
    </div>

    <div class="abs van" role="img" aria-label="Company service van in maroon and black livery"></div>

    <div class="abs schedule">
      <svg width="290" height="230" viewBox="0 0 290 230" aria-hidden="true">
        <polygon points="0,95 290,95 270,160 290,225 0,225 20,160" fill="var(--maroon)" stroke="var(--orange)" stroke-width="6"/>
        <circle cx="145" cy="55" r="44" fill="var(--orange)" stroke="var(--white)" stroke-width="6"/>
        <circle cx="145" cy="58" r="28" fill="none" stroke="var(--white)" stroke-width="6"/>
        <line x1="145" y1="58" x2="145" y2="42" stroke="var(--white)" stroke-width="5" stroke-linecap="round"/>
        <line x1="145" y1="58" x2="157" y2="64" stroke="var(--white)" stroke-width="5" stroke-linecap="round"/>
        <line x1="115" y1="24" x2="126" y2="33" stroke="var(--white)" stroke-width="6" stroke-linecap="round"/>
        <line x1="175" y1="24" x2="164" y2="33" stroke="var(--white)" stroke-width="6" stroke-linecap="round"/>
      </svg>
      <div class="abs schedule-label">Schedule<br>A SERVICE!</div>
    </div>

    <h1 class="abs headline">Most Trusted Heating &amp; Cooling Company</h1>
    <a class="abs learn-more">LEARN MORE</a>

    <svg class="abs service-band" width="1200" height="230" viewBox="0 0 1200 230" aria-hidden="true">
      <path d="M0,0 H1200 V180 H760 Q640,180 600,115 Q560,180 440,180 H0 Z" fill="var(--navy)"/>
    </svg>

    <div class="abs services">
      <div class="service" style="left:45px">
        <svg width="203" height="203" viewBox="0 0 203 203" aria-hidden="true">
          <rect x="10" y="10" width="183" height="183" rx="50" fill="var(--maroon)" stroke="var(--orange)" stroke-width="10"/>
          <circle cx="101" cy="101" r="30" fill="none" stroke="var(--white)" stroke-width="8"/>
          <g stroke="var(--white)" stroke-width="8" stroke-linecap="round">
            <line x1="101" y1="45" x2="101" y2="58"/><line x1="101" y1="144" x2="101" y2="157"/>
            <line x1="45" y1="101" x2="58" y2="101"/><line x1="144" y1="101" x2="157" y2="101"/>
            <line x1="61" y1="61" x2="70" y2="70"/><line x1="132" y1="132" x2="141" y2="141"/>
            <line x1="141" y1="61" x2="132" y2="70"/><line x1="70" y1="132" x2="61" y2="141"/>
          </g>
        </svg>
        <div class="service-name">HEATING</div>
      </div>
      <div class="service" style="left:310px">
        <svg width="203" height="203" viewBox="0 0 203 203" aria-hidden="true">
          <rect x="10" y="10" width="183" height="183" rx="50" fill="var(--maroon)" stroke="var(--orange)" stroke-width="10"/>
          <g stroke="var(--white)" stroke-width="8" stroke-linecap="round">
            <line x1="101" y1="50" x2="101" y2="152"/>
            <line x1="57" y1="76" x2="145" y2="126"/>
            <line x1="57" y1="126" x2="145" y2="76"/>
            <polyline points="88,58 101,70 114,58" fill="none"/>
            <polyline points="88,144 101,132 114,144" fill="none"/>
          </g>
        </svg>
        <div class="service-name">AIR<br>CONDITIONING</div>
      </div>
      <div class="service" style="left:624px">
        <svg width="203" height="203" viewBox="0 0 203 203" aria-hidden="true">
          <rect x="10" y="10" width="183" height="183" rx="50" fill="var(--maroon)" stroke="var(--orange)" stroke-width="10"/>
          <rect x="64" y="50" width="76" height="102" rx="6" fill="none" stroke="var(--white)" stroke-width="8"/>
          <g stroke="var(--white)" stroke-width="7" stroke-linecap="round">
            <line x1="80" y1="78" x2="124" y2="78"/><line x1="80" y1="100" x2="124" y2="100"/><line x1="80" y1="122" x2="110" y2="122"/>
          </g>
        </svg>
        <div class="service-name">OTHER SERVICES</div>
      </div>
      <div class="service" style="left:924px">
        <svg width="203" height="203" viewBox="0 0 203 203" aria-hidden="true">
          <rect x="10" y="10" width="183" height="183" rx="50" fill="var(--maroon)" stroke="var(--orange)" stroke-width="10"/>
          <g fill="var(--white)">
            <circle cx="66" cy="96" r="18"/><circle cx="101" cy="86" r="21"/><circle cx="136" cy="96" r="18"/>
            <rect x="44" y="120" width="115" height="32" rx="14"/>
          </g>
        </svg>
        <div class="service-name">WHO WE ARE</div>
      </div>
    </div>
  </section>

  <section aria-label="Latest news">
    <div class="abs news" role="img" aria-label="Photo of a family walking along a beach at dusk"></div>
    <div class="abs news-shade"></div>
    <article class="abs news-item" style="left:116px">
      <h2 class="news-date">August 26</h2>
      <p class="news-text">Lorem Ipsum has been the industry's standard dummy text ever since the 1500s, when an unknown printer took a galley</p>
    </article>
    <article class="abs news-item" style="left:649px">
      <h2 class="news-date">July 15</h2>
      <p class="news-text">Lorem Ipsum has been the industry's standard dummy text ever since the 1500s, when an unknown printer took a galley</p>
    </article>
  </section>

  <footer>
    <div class="abs divider"></div>
    <div class="abs footer-left"></div>
    <div class="abs footer-right"></div>
    <div class="abs brand brand-plate"><span class="brand-dot"></span>Hearthline Climate</div>

    <address class="abs contact">
      42 Maple Ridge Lane<br>Lakeview, NJ 07000<br>555 010 2040<br>info@hearthlineclimate.com
    </address>
    <div class="abs stay">STAY CONNECTED</div>
    <div class="abs social" aria-label="Social links"><span></span><span></span><span></span></div>

    <ul class="abs nav-list nav-main">
      <li>Home</li><li>About</li><li>Services</li><li>Testimonials</li><li>Blog</li><li>Contact</li>
      <li class="gap"></li>
      <li>Heating</li><li>New Installation</li><li>Repair &amp; Service</li><li>Heat Pumps</li><li>Boilers</li><li>Radiant Heat Systems</li>
    </ul>
    <ul class="abs nav-list nav-sub">
      <li>Air Conditioning</li><li>New Installation</li><li>Repair &amp; Service</li><li>Ductless Systems</li>
      <li class="gap-sm"></li>
      <li>Other Services</li><li>Indoor Air Quality</li><li>Thermostats &amp; Zoning</li><li>Generators</li><li>Products</li>
      <li class="gap-sm"></li>
      <li>Who We Service</li><li>Residental &amp; Homeowners</li><li>Commercial Businesses</li>
    </ul>
  </footer>

</div>
</body>
</html>
```